Thornvale Group needs a business card design

We need a new business card design using the logo recently selected in a logo competition on Pixel Bazaar. Our business is a consultancy specializing in aviation and energy and the winning business card design will promote an image of precision and professionalism with creativity.

Please use the logo with the name on the front of the card and use a complementary font. Make the back white with either the light grey or dark grey logo.

Target Market(s)

Senior finance and legal leaders at aviation and energy companies

Industry/Entity Type

Management Consulting

Contact Information for Business Card

Peter Castrell
President
Thornvale Group

www.thornvalegroup.example

(555) 204-6391
pc@thornvalegroup.example

Requirements
Must have
• Professional font that goes well with the logo font

```html
<!DOCTYPE html>
<html lang="en">
<head>
<meta charset="utf-8">
<title>Thornvale Group – Business Card</title>
<link rel="stylesheet" href="https://fonts.googleapis.com/css2?family=Open+Sans:wght@400;600;700&display=swap">
<style>
  :root {
    --backdrop: #eceae6;
    --card: #ffffff;
    --navy: #1c4677;
    --ink: #2a2f36;
    --pattern-light: #e4e9ef;
    --pattern-mid: #ccd5df;
    --shadow: rgba(40, 40, 40, 0.18);
  }
  * { margin: 0; padding: 0; box-sizing: border-box; }
  html, body {
    width: 1200px;
    height: 900px;
    overflow: hidden;
    background: var(--backdrop);
    font-family: "Open Sans", Arial, sans-serif;
  }
  .canvas {
    position: relative;
    width: 1200px;
    height: 900px;
  }
  .card {
    position: absolute;
    top: 296px;
    width: 540px;
    height: 309px;
    background: var(--card);
    box-shadow: 0 6px 18px var(--shadow);
    overflow: hidden;
  }
  .card--back { left: 50px; }
  .card--front { left: 610px; }

  /* Back: pattern area fades out toward the lower right, where the name sits on white */
  .pattern-field {
    position: absolute;
    inset: 0;
    background:
      radial-gradient(ellipse 330px 170px at 100% 100%, var(--card) 0%, var(--card) 45%, rgba(255,255,255,0) 100%),
      repeating-linear-gradient(120deg, var(--pattern-mid) 0 18px, var(--pattern-light) 18px 46px);
  }
  .back-name {
    position: absolute;
    right: 34px;
    bottom: 52px;
    color: var(--navy);
    font-size: 21px;
    font-weight: 400;
    letter-spacing: 0.12em;
    text-transform: uppercase;
  }

  /* Front */
  .contact {
    position: absolute;
    left: 318px;
    top: 26px;
    color: var(--ink);
  }
  .contact-name {
    color: var(--navy);
    font-size: 17px;
    font-weight: 700;
    line-height: 1.2;
  }
  .contact-title {
    font-size: 12px;
    font-weight: 400;
    margin-top: 1px;
  }
  .contact-list {
    list-style: none;
    margin-top: 14px;
    font-size: 11.5px;
  }
  .contact-list li {
    display: flex;
    align-items: center;
    gap: 8px;
    margin-bottom: 5px;
    white-space: nowrap;
  }
  .contact-icon { width: 11px; height: 11px; fill: var(--navy); flex: none; }
  .front-brand {
    position: absolute;
    left: 48px;
    bottom: 60px;
    display: flex;
    align-items: center;
    gap: 14px;
  }
  .brand-mark {
    width: 22px;
    height: 22px;
    background: var(--navy);
  }
  .brand-name {
    color: var(--navy);
    font-size: 30px;
    font-weight: 400;
    letter-spacing: 0.1em;
    text-transform: uppercase;
  }
</style>
</head>
<body>
<main class="canvas">
  <section class="card card--back" aria-label="Card back">
    <div class="pattern-field" role="img" aria-label="Repeating pale grey-blue brand motif pattern"></div>
    <p class="back-name">Thornvale Group</p>
  </section>

  <section class="card card--front" aria-label="Card front">
    <div class="contact">
      <p class="contact-name">Peter Castrell</p>
      <p class="contact-title">President</p>
      <ul class="contact-list">
        <li>
          <svg class="contact-icon" viewBox="0 0 24 24" aria-hidden="true"><path d="M6.6 10.8c1.4 2.8 3.8 5.1 6.6 6.6l2.2-2.2c.3-.3.7-.4 1-.2 1.1.4 2.3.6 3.6.6.6 0 1 .4 1 1V20c0 .6-.4 1-1 1C10.6 21 3 13.4 3 4c0-.6.4-1 1-1h3.5c.6 0 1 .4 1 1 0 1.3.2 2.5.6 3.6.1.3 0 .7-.2 1L6.6 10.8z"/></svg>
          <span>(555) 204-6391</span>
        </li>
        <li>
          <svg class="contact-icon" viewBox="0 0 24 24" aria-hidden="true"><path d="M2 5h20v14H2V5zm2 2v.5l8 5 8-5V7H4zm16 2.8-8 5-8-5V17h16V9.8z"/></svg>
          <span>pc@thornvalegroup.example</span>
        </li>
        <li>
          <svg class="contact-icon" viewBox="0 0 24 24" aria-hidden="true"><path d="M12 2a10 10 0 1 0 0 20 10 10 0 0 0 0-20zm6.9 6h-2.9a15 15 0 0 0-1.3-3.6A8 8 0 0 1 18.9 8zM12 4c.8 1.2 1.5 2.5 1.9 4h-3.8c.4-1.5 1.1-2.8 1.9-4zM4.3 14a8 8 0 0 1 0-4h3.4a16 16 0 0 0 0 4H4.3zm.8 2h2.9c.3 1.3.8 2.5 1.3 3.6A8 8 0 0 1 5.1 16zM8 8H5.1a8 8 0 0 1 4.2-3.6C8.8 5.5 8.3 6.7 8 8zm4 12c-.8-1.2-1.5-2.5-1.9-4h3.8c-.4 1.5-1.1 2.8-1.9 4zm2.3-6H9.7a14 14 0 0 1 0-4h4.6a14 14 0 0 1 0 4zm.4 5.6c.5-1.1 1-2.3 1.3-3.6h2.9a8 8 0 0 1-4.2 3.6zM16.3 14a16 16 0 0 0 0-4h3.4a8 8 0 0 1 0 4h-3.4z"/></svg>
          <span>www.thornvalegroup.example</span>
        </li>
      </ul>
    </div>
    <div class="front-brand">
      <span class="brand-mark" aria-hidden="true"></span>
      <p class="brand-name">Thornvale Group</p>
    </div>
  </section>
</main>
</body>
</html>
```